Photography business - business card design quick turn around

Create a business card design for me please. I actually need the final design back before the end of Sunday 13th May 7pm GMT. Sorry for the short notice.

Photoshop artwork template uploaded with artwork guidelines including printer profiles and other mandatory specifications. Only one side of the business card is required as the other side will be an image.

The design is required as an unflattened PSD file so that I can edit the text if I need to.

My brand colours are white and the teal you see in the logo. Occasionally I also use a dark grey on my website (I don't mind the shade of grey as appreciate grey on teal would be a different grey, to the grey I use on white on the website, so just use a shade of grey that matches). Font can be as the font for the logo or if you prefer I am open to another sans serif, easily legible font. Ideally font size will be 12+.Please do not use capital letters for text. I prefer everything to be lower case, if possible.

Thank you.

Lena

Target Market(s)

Other business owners who may refer me and families

Industry/Entity Type

Photographer

Contact Information for Business Card

Silver Kettle Photography Logo
Sub text: family portraiture, captured with love

Contact information, ideally using simple icons to represent email / website / facebook / instagram / pinterest

email: lena@silverkettlephotography.co.uk
website: silverkettlephotography.co.uk
facebook: @silverkettlephotography
pinterest: pinfolio.com/silverkettlepho
instagram: @silverkettle_photography
mobile/telephone: 07713460291

If there is too much text then please drop the instagram and pinterest information.

Font styles to use
Sans Serif

Colors
33b8a4

Requirements
Must have
• Logo
• Contact details as listed above
• sub text
Nice to have
• Instagram and Pinterest contact details
• Nice to have icons to represent website / phone / facebook etc followered by the handle where relevant

```html
<!DOCTYPE html>
<html lang="en">
<head>
<meta charset="utf-8">
<title>Silver Kettle Photography – Business Card</title>
<link rel="stylesheet" href="https://fonts.googleapis.com/css2?family=Questrial&family=Pinyon+Script&display=swap">
<style>
  :root {
    --teal: #33b8a4;
    --grey-card: #3a3a3c;
    --grey-text: #cfcfcf;
    --white: #ffffff;
    --paper: #f4f4f4;
    --backdrop: #1e1e1f;
  }
  html, body {
    margin: 0;
    width: 1200px;
    height: 873px;
    overflow: hidden;
    background: var(--backdrop);
  }
  .stage {
    position: relative;
    width: 1200px;
    height: 873px;
  }
  .card {
    position: absolute;
    left: 150px;
    top: 180px;
    width: 900px;
    height: 514px;
    background: linear-gradient(180deg, var(--white), var(--paper));
    overflow: hidden;
    box-shadow: 0 18px 40px rgba(0,0,0,.55);
    font-family: "Questrial", sans-serif;
  }
  .card-wave {
    position: absolute;
    inset: 0;
    width: 900px;
    height: 514px;
  }
  .brand {
    position: absolute;
    right: 70px;
    top: 78px;
    display: flex;
    align-items: center;
    gap: 16px;
  }
  .brand-mark {
    width: 46px;
    height: 46px;
    border-radius: 50%;
    background: var(--teal);
  }
  .brand-name {
    color: var(--teal);
    font-size: 30px;
    font-weight: 400;
    line-height: 1.1;
    letter-spacing: .5px;
    margin: 0;
  }
  .contact-list {
    position: absolute;
    left: 58px;
    top: 322px;
    margin: 0;
    padding: 0;
    list-style: none;
  }
  .contact-item {
    display: flex;
    align-items: center;
    gap: 14px;
    height: 34px;
    color: var(--grey-text);
    font-size: 18px;
    white-space: nowrap;
  }
  .contact-icon {
    width: 20px;
    height: 20px;
    flex: none;
  }
  .contact-dot {
    width: 14px;
    height: 14px;
    margin: 0 3px;
    border-radius: 50%;
    background: var(--teal);
    flex: none;
  }
  .card-tagline {
    position: absolute;
    right: 60px;
    top: 336px;
    margin: 0;
    color: var(--grey-text);
    font-family: "Pinyon Script", cursive;
    font-size: 28px;
    white-space: nowrap;
  }
  .card-website {
    position: absolute;
    right: 60px;
    top: 388px;
    margin: 0;
    color: var(--teal);
    font-size: 18px;
    font-weight: 400;
    letter-spacing: .3px;
    white-space: nowrap;
  }
</style>
</head>
<body>
<main class="stage">
  <article class="card">
    <svg class="card-wave" viewBox="0 0 900 514" aria-hidden="true">
      <path d="M0,262 C220,214 470,242 900,158 L900,514 L0,514 Z" fill="var(--teal)"/>
      <path d="M0,282 C240,232 500,262 900,186 L900,514 L0,514 Z" fill="var(--grey-card)"/>
    </svg>

    <div class="brand">
      <span class="brand-mark" aria-hidden="true"></span>
      <p class="brand-name">Silver Kettle<br>Photography</p>
    </div>

    <ul class="contact-list">
      <li class="contact-item">
        <svg class="contact-icon" viewBox="0 0 20 20" aria-hidden="true">
          <path d="M4 2h4l1.5 4-2.2 1.4a11 11 0 0 0 5.3 5.3L14 10.5l4 1.5v4a2 2 0 0 1-2 2A15 15 0 0 1 2 4a2 2 0 0 1 2-2z" fill="var(--teal)"/>
        </svg>
        07713460291
      </li>
      <li class="contact-item">
        <svg class="contact-icon" viewBox="0 0 20 20" aria-hidden="true">
          <rect x="1" y="4" width="18" height="12" rx="1.5" fill="var(--teal)"/>
          <path d="M2 5l8 6 8-6" fill="none" stroke="var(--grey-card)" stroke-width="1.6"/>
        </svg>
        lena@silverkettlephotography.co.uk
      </li>
      <li class="contact-item">
        <span class="contact-dot" aria-hidden="true"></span>
        @silverkettlephotography
      </li>
      <li class="contact-item">
        <span class="contact-dot" aria-hidden="true"></span>
        pinfolio.com/silverkettlepho
      </li>
      <li class="contact-item">
        <span class="contact-dot" aria-hidden="true"></span>
        @silverkettle_photography
      </li>
    </ul>

    <p class="card-tagline">Family Portraiture, Captured with Love</p>
    <p class="card-website">www.silverkettlephotography.co.uk</p>
  </article>
</main>
</body>
</html>
```